mechanical repair shop

our shop repairs light and medium duty trucks

we sell tires , do oil changes, engine and transmissions
vehicle accessories, alignments, brakes , exhaust, all major and minor repairs.
Updates

if you would like to get a hold of me email: milo.hensworth@quarrytide.net tel: 1-780-555-0148

Target Market(s)

light and medium duty trucks and cars

Industry/Entity Type

Shop

Colors
f37122

Requirements
Must have
• visual sales displays
Nice to have
• pictures

```html
<!DOCTYPE html>
<html lang="en">
<head>
<meta charset="utf-8">
<title>Ridgeway Fleet Services – Truck Repair Flyer</title>
<link href="https://fonts.googleapis.com/css2?family=Oswald:wght@300;400;500;700&family=Montserrat:ital,wght@0,400;0,500;1,400&display=swap" rel="stylesheet">
<style>
  :root{
    --orange:#f37122;
    --black:#0b0b0b;
    --white:#ffffff;
    --ink:#1d1d1d;
    --page:#2a2a2a;
  }
  *{box-sizing:border-box;margin:0;padding:0}
  html,body{width:960px;height:1200px;overflow:hidden;background:var(--page)}
  .flyer{position:absolute;left:56px;top:0;width:848px;height:1200px;background:var(--black);overflow:hidden;font-family:"Montserrat",sans-serif;color:var(--ink)}
  .flyer-shapes{position:absolute;inset:0}
  .photo{position:absolute}
  .truck-photo{left:30px;top:45px;width:485px;height:335px;border-radius:6px;background:linear-gradient(160deg,#f4f4f4 0%,#dcdcdc 55%,#8a8a8a 85%,#2b2b2b 100%)}
  .round-photo{border-radius:50%;border:7px solid var(--orange);box-shadow:0 0 0 4px var(--white)}
  .tire-photo{left:40px;top:376px;width:310px;height:310px;background:radial-gradient(circle at 55% 60%,#2a2a2a 0%,#4a4a4a 35%,#9a9a9a 70%,#cfcfcf 100%)}
  .oil-photo{left:240px;top:993px;width:180px;height:180px;background:radial-gradient(circle at 50% 45%,#d9a12a 0%,#8b7a52 25%,#6c6c6c 55%,#b8b8b8 100%)}
  .brand-badge{position:absolute;left:524px;top:52px;width:254px;height:196px;border-radius:50%;background:var(--black);border:3px solid var(--orange);display:flex;align-items:center;justify-content:center;text-align:center}
  .brand-name{font-family:"Oswald",sans-serif;font-weight:500;color:var(--white);font-size:27px;line-height:1.15;letter-spacing:.5px}
  .headline{position:absolute;left:550px;top:345px;font-family:"Oswald",sans-serif;font-weight:700;font-size:31px;line-height:40px;color:var(--white);letter-spacing:-.3px}
  .headline .accent{color:var(--orange)}
  .services{position:absolute;left:440px;top:535px;width:400px}
  .services-title{font-family:"Oswald",sans-serif;font-weight:400;font-size:38px;color:var(--orange);letter-spacing:-.5px;margin-bottom:14px}
  .service-list{list-style:none}
  .service-list li{display:flex;align-items:center;gap:11px;height:32.7px;font-size:15px;color:var(--ink)}
  .service-list svg{flex:none}
  .about{position:absolute;left:30px;top:713px;width:352px;font-size:13.4px;line-height:24.2px;font-style:italic;text-align:justify;color:var(--ink)}
  .website{position:absolute;left:38px;top:1147px;font-family:"Oswald",sans-serif;font-weight:300;font-size:23px;color:var(--white)}
  .contact{position:absolute;right:41px;top:1088px;text-align:right}
  .contact-lead{font-family:"Oswald",sans-serif;font-weight:400;font-size:24px;color:var(--orange)}
  .contact-phone{display:flex;align-items:center;justify-content:flex-end;gap:8px;font-family:"Oswald",sans-serif;font-weight:300;font-size:45px;line-height:52px;color:var(--white)}
</style>
</head>
<body>
<main class="flyer">
  <svg class="flyer-shapes" width="848" height="1200" viewBox="0 0 848 1200" aria-hidden="true">
    <path fill="var(--white)" d="M338,0 H848 V262 C740,300 620,330 520,336 C470,338 430,334 410,330 C390,200 360,80 338,0 Z"/>
    <path fill="var(--orange)" d="M540,332 C650,318 760,285 848,232 V262 C760,300 650,326 540,332 Z"/>
    <path fill="var(--white)" d="M0,600 C60,520 150,470 260,470 C420,470 700,480 848,535 V1010 C700,1060 500,1095 330,1102 C200,1104 80,1098 0,1092 Z"/>
    <path fill="var(--orange)" d="M340,488 C450,476 560,482 612,498 C520,492 430,492 340,497 Z"/>
    <path fill="var(--orange)" d="M0,565 C15,545 30,530 52,522 C36,548 20,578 0,612 Z"/>
    <path fill="var(--orange)" d="M0,1020 C80,1058 170,1088 250,1106 C150,1100 70,1088 0,1076 Z"/>
  </svg>

  <div class="photo truck-photo" role="img" aria-label="White light-duty box truck with company mark on the cargo box"></div>

  <div class="brand-badge">
    <span class="brand-name">RIDGEWAY<br>Fleet Services Ltd.</span>
  </div>

  <h1 class="headline">YOUR COMPLETE <span class="accent">LIGHT</span><br><span class="accent">MEDIUM DUTY TRUCK</span><br>REPAIR FACILITY</h1>

  <div class="photo round-photo tire-photo" role="img" aria-label="Mechanic mounting a tire on a tire changing machine"></div>

  <section class="services">
    <h2 class="services-title">Services We Offer:</h2>
    <ul class="service-list">
      <li><svg width="15" height="15" viewBox="0 0 16 16"><circle cx="8" cy="8" r="6.5" fill="none" stroke="var(--orange)" stroke-width="1.6"/><path d="M4.8 8.2 L7.3 10.6 L14 3.4" fill="none" stroke="var(--orange)" stroke-width="1.8"/></svg>Factory recommended service/maintenance</li>
      <li><svg width="15" height="15" viewBox="0 0 16 16"><circle cx="8" cy="8" r="6.5" fill="none" stroke="var(--orange)" stroke-width="1.6"/><path d="M4.8 8.2 L7.3 10.6 L14 3.4" fill="none" stroke="var(--orange)" stroke-width="1.8"/></svg>Oil change</li>
      <li><svg width="15" height="15" viewBox="0 0 16 16"><circle cx="8" cy="8" r="6.5" fill="none" stroke="var(--orange)" stroke-width="1.6"/><path d="M4.8 8.2 L7.3 10.6 L14 3.4" fill="none" stroke="var(--orange)" stroke-width="1.8"/></svg>Fuel system repair and maintenance</li>
      <li><svg width="15" height="15" viewBox="0 0 16 16"><circle cx="8" cy="8" r="6.5" fill="none" stroke="var(--orange)" stroke-width="1.6"/><path d="M4.8 8.2 L7.3 10.6 L14 3.4" fill="none" stroke="var(--orange)" stroke-width="1.8"/></svg>Battery system diagnosis &amp; repair</li>
      <li><svg width="15" height="15" viewBox="0 0 16 16"><circle cx="8" cy="8" r="6.5" fill="none" stroke="var(--orange)" stroke-width="1.6"/><path d="M4.8 8.2 L7.3 10.6 L14 3.4" fill="none" stroke="var(--orange)" stroke-width="1.8"/></svg>Check engine light</li>
      <li><svg width="15" height="15" viewBox="0 0 16 16"><circle cx="8" cy="8" r="6.5" fill="none" stroke="var(--orange)" stroke-width="1.6"/><path d="M4.8 8.2 L7.3 10.6 L14 3.4" fill="none" stroke="var(--orange)" stroke-width="1.8"/></svg>Electrical problems</li>
      <li><svg width="15" height="15" viewBox="0 0 16 16"><circle cx="8" cy="8" r="6.5" fill="none" stroke="var(--orange)" stroke-width="1.6"/><path d="M4.8 8.2 L7.3 10.6 L14 3.4" fill="none" stroke="var(--orange)" stroke-width="1.8"/></svg>Engine performance</li>
      <li><svg width="15" height="15" viewBox="0 0 16 16"><circle cx="8" cy="8" r="6.5" fill="none" stroke="var(--orange)" stroke-width="1.6"/><path d="M4.8 8.2 L7.3 10.6 L14 3.4" fill="none" stroke="var(--orange)" stroke-width="1.8"/></svg>Exhaust problems</li>
      <li><svg width="15" height="15" viewBox="0 0 16 16"><circle cx="8" cy="8" r="6.5" fill="none" stroke="var(--orange)" stroke-width="1.6"/><path d="M4.8 8.2 L7.3 10.6 L14 3.4" fill="none" stroke="var(--orange)" stroke-width="1.8"/></svg>Tires</li>
      <li><svg width="15" height="15" viewBox="0 0 16 16"><circle cx="8" cy="8" r="6.5" fill="none" stroke="var(--orange)" stroke-width="1.6"/><path d="M4.8 8.2 L7.3 10.6 L14 3.4" fill="none" stroke="var(--orange)" stroke-width="1.8"/></svg>30/60/90 K mileage maintenance services</li>
      <li><svg width="15" height="15" viewBox="0 0 16 16"><circle cx="8" cy="8" r="6.5" fill="none" stroke="var(--orange)" stroke-width="1.6"/><path d="M4.8 8.2 L7.3 10.6 L14 3.4" fill="none" stroke="var(--orange)" stroke-width="1.8"/></svg>Cooling system repair and maintenance</li>
      <li><svg width="15" height="15" viewBox="0 0 16 16"><circle cx="8" cy="8" r="6.5" fill="none" stroke="var(--orange)" stroke-width="1.6"/><path d="M4.8 8.2 L7.3 10.6 L14 3.4" fill="none" stroke="var(--orange)" stroke-width="1.8"/></svg>Air conditioning / heating repair</li>
      <li><svg width="15" height="15" viewBox="0 0 16 16"><circle cx="8" cy="8" r="6.5" fill="none" stroke="var(--orange)" stroke-width="1.6"/><path d="M4.8 8.2 L7.3 10.6 L14 3.4" fill="none" stroke="var(--orange)" stroke-width="1.8"/></svg>Brake system</li>
      <li><svg width="15" height="15" viewBox="0 0 16 16"><circle cx="8" cy="8" r="6.5" fill="none" stroke="var(--orange)" stroke-width="1.6"/><path d="M4.8 8.2 L7.3 10.6 L14 3.4" fill="none" stroke="var(--orange)" stroke-width="1.8"/></svg>Steering &amp; suspension</li>
    </ul>
  </section>

  <p class="about">Ridgeway Fleet Services Ltd. has set up and successfully operates a complete equipment repair facility. First set up to be a dedicated repair shop for a single large client, Ridgeway has now expanded to include all manner of clients with diverse equipment needs. With Journeyman and Apprentice HD mechanics available 24 hours a day our facility is ready to handle all of your equipment needs. We are an ‘approved’ repair facility for a growing list of equipment manufacturers including: Ironvale, Kestrel, Lumenlift, TRX, Highpeak etc.</p>

  <div class="photo round-photo oil-photo" role="img" aria-label="Fresh motor oil being poured into an engine"></div>

  <div class="website">www.ridgewayfleet.com</div>

  <div class="contact">
    <div class="contact-lead">Call us for more information</div>
    <div class="contact-phone">
      <svg width="26" height="40" viewBox="0 0 26 40" aria-hidden="true"><path fill="var(--white)" d="M6 2 C3 3 1 6 1 10 C1 20 6 31 13 37 C15 39 18 39 20 37 L23 34 C24 33 24 31 23 30 L19 25 C18 24 16 24 15 25 L13 27 C10 23 8 18 7 13 L10 12 C11 11 12 10 11 8 L10 3 C9 2 8 1 6 2 Z"/></svg>
      <span>780 555 0172</span>
    </div>
  </div>
</main>
</body>
</html>
```